Brookmere Osteopathy flyer

I want a clean clear DL flyer (but also want an A4 poster) promoting a new Osteopathic business in a semi rural area in Tasmania (Australia).
It can have pictures like the examples attached to show people what Osteopathy is (its like Chiropractic and physiotherapy).
I am the sole practioner and am male, so any pictures would be best to be a white male if possible.
I've attached some wording, you can use all, or none of it
I don't have a phone number for the business yet
info@brookmereosteopathy.example
www.brookmereosteopathy.example
Target Market(s)
Australians, from tradies, professionals, babies to retired people
Industry/Entity Type
Health
Look and feel

```html
<!DOCTYPE html>
<html lang="en">
<head>
<meta charset="utf-8">
<title>Brookmere Osteopathy Flyer</title>
<link href="https://fonts.googleapis.com/css2?family=Roboto+Condensed:wght@400;700&family=Arimo:wght@400&display=swap" rel="stylesheet">
<style>
  :root {
    --canvas: #d6d6d6;
    --paper-light: #f4f4f4;
    --paper-mid: #dedede;
    --silver-dark: #7a7a7a;
    --silver-light: #fbfbfb;
    --ink: #151515;
    --photo-skin: #c79a72;
    --photo-blue: #3f7c98;
    --photo-grey: #e4e6e8;
  }
  html, body {
    margin: 0;
    width: 1200px;
    height: 849px;
    overflow: hidden;
    background: var(--canvas);
  }
  .flyer {
    position: absolute;
    top: 223px;
    display: flex;
    gap: 20px;
    left: 20px;
  }
  .spread {
    width: 570px;
    height: 403px;
    display: block;
    box-shadow: 0 2px 8px rgba(0,0,0,0.18);
  }
  .heading { font-family: "Roboto Condensed", sans-serif; font-weight: 700; font-size: 19px; fill: var(--ink); }
  .subheading { font-family: "Arimo", sans-serif; font-size: 14px; fill: var(--ink); }
  .reason-list { font-family: "Roboto Condensed", sans-serif; font-weight: 700; font-size: 13px; fill: var(--ink); letter-spacing: 0.3px; }
  .intro-copy { font-family: "Arimo", sans-serif; font-size: 10.5px; fill: var(--ink); }
  .brand-name { font-family: "Roboto Condensed", sans-serif; font-weight: 700; font-size: 17px; fill: var(--ink); letter-spacing: 1px; }
  .contact-line { font-family: "Arimo", sans-serif; font-size: 11.5px; fill: var(--ink); letter-spacing: 0.6px; }
  .web-address { font-family: "Roboto Condensed", sans-serif; font-weight: 700; font-size: 14px; fill: var(--ink); letter-spacing: 0.6px; }
</style>
</head>
<body>
<main class="flyer">

  <!-- Inside spread -->
  <svg class="spread spread--inside" viewBox="0 0 973 688" xmlns="http://www.w3.org/2000/svg">
    <defs>
      <linearGradient id="paper" x1="0" y1="0" x2="1" y2="1">
        <stop offset="0" stop-color="var(--paper-light)"/>
        <stop offset="1" stop-color="var(--paper-mid)"/>
      </linearGradient>
      <linearGradient id="silver" x1="0" y1="0" x2="0" y2="1">
        <stop offset="0" stop-color="var(--silver-dark)"/>
        <stop offset="0.45" stop-color="var(--silver-light)"/>
        <stop offset="0.7" stop-color="#a9a9a9"/>
        <stop offset="1" stop-color="var(--silver-dark)"/>
      </linearGradient>
      <linearGradient id="treatmentTones" x1="0" y1="0" x2="1" y2="1">
        <stop offset="0" stop-color="var(--photo-grey)"/>
        <stop offset="0.5" stop-color="var(--photo-skin)"/>
        <stop offset="1" stop-color="#2a2f36"/>
      </linearGradient>
      <linearGradient id="figureTones" x1="0" y1="0" x2="0" y2="1">
        <stop offset="0" stop-color="#ececec"/>
        <stop offset="0.5" stop-color="#dcc2a0"/>
        <stop offset="1" stop-color="#e6e6e6"/>
      </linearGradient>
      <linearGradient id="backPainTones" x1="0" y1="0" x2="0" y2="1">
        <stop offset="0" stop-color="#e8e8e8"/>
        <stop offset="0.25" stop-color="#3b97c4"/>
        <stop offset="0.6" stop-color="#d98a7a"/>
        <stop offset="1" stop-color="#5a5a5a"/>
      </linearGradient>
    </defs>

    <rect class="panel-bg" width="973" height="688" fill="url(#paper)"/>

    <path class="photo photo--treatment" role="img" aria-label="Photo of a practitioner stretching a woman's shoulder on a treatment table"
          d="M0,0 H500 V40 C360,120 180,172 0,160 Z" fill="url(#treatmentTones)"/>

    <path class="band band--top" d="M-10,160 C180,172 360,120 500,40 C560,8 640,10 700,18 C800,30 880,70 983,100"
          fill="none" stroke="url(#silver)" stroke-width="30"/>

    <rect class="photo photo--figure" role="img" aria-label="Photo of a wooden posable figure leaning forward"
          x="386" y="98" width="240" height="400" fill="url(#figureTones)" opacity="0.85"/>

    <path class="band band--bottom" d="M-10,505 C150,478 330,470 480,520 C620,568 700,650 760,700"
          fill="none" stroke="url(#silver)" stroke-width="34"/>

    <rect class="photo photo--back-pain" role="img" aria-label="Photo of a man holding his lower back with a glowing spine overlay"
          x="656" y="218" width="317" height="470" fill="url(#backPainTones)"/>

    <g class="brand-mark" transform="translate(690,140)">
      <circle cx="10" cy="12" r="9" fill="none" stroke="var(--ink)" stroke-width="2"/>
      <text class="brand-name" x="26" y="8">BROOKMERE</text>
      <text class="brand-name" x="26" y="28">OSTEOPATHY</text>
    </g>

    <text class="heading" x="39" y="232">COMMON REASONS</text>
    <text class="subheading" x="39" y="250">PEOPLE VISIT AN OSTEOPATH:</text>
    <g class="reason-list">
      <text x="39" y="272">•  Back / neck pain</text>
      <text x="39" y="290">•  Headaches / migraines</text>
      <text x="39" y="307">•  Joint and muscle pain</text>
      <text x="39" y="325">•  Pregnancy-related discomfort</text>
      <text x="39" y="343">•  Disc related issues</text>
      <text x="39" y="360">•  Sciatica</text>
      <text x="39" y="378">•  Plantar fasciitis</text>
      <text x="39" y="396">•  Tendonitis / Bursitis</text>
      <text x="39" y="413">•  Adhesive capsulitis (frozen shoulder)</text>
      <text x="39" y="431">•  Tennis / Golfers elbow</text>
    </g>

    <g class="intro-copy">
      <text x="39" y="579">Osteopaths use a combination of joint</text>
      <text x="39" y="593">manipulation, targeted deep tissue massage</text>
      <text x="39" y="607">and stretching to improve function, relieve pain</text>
      <text x="39" y="621">and support the body’s ability to heal itself.</text>
    </g>
  </svg>

  <!-- Outside spread -->
  <svg class="spread spread--outside" viewBox="0 0 973 688" xmlns="http://www.w3.org/2000/svg">
    <defs>
      <linearGradient id="paperOut" x1="0" y1="0" x2="1" y2="1">
        <stop offset="0" stop-color="var(--paper-light)"/>
        <stop offset="1" stop-color="var(--paper-mid)"/>
      </linearGradient>
      <linearGradient id="silverOut" x1="0" y1="0" x2="0" y2="1">
        <stop offset="0" stop-color="var(--silver-dark)"/>
        <stop offset="0.45" stop-color="var(--silver-light)"/>
        <stop offset="0.7" stop-color="#a9a9a9"/>
        <stop offset="1" stop-color="var(--silver-dark)"/>
      </linearGradient>
      <linearGradient id="massageTones" x1="0" y1="0" x2="1" y2="0.4">
        <stop offset="0" stop-color="#d8e2e8"/>
        <stop offset="0.35" stop-color="var(--photo-skin)"/>
        <stop offset="0.6" stop-color="var(--photo-blue)"/>
        <stop offset="1" stop-color="#4a3428"/>
      </linearGradient>
    </defs>

    <rect class="panel-bg" width="973" height="688" fill="url(#paperOut)"/>

    <path class="photo photo--massage" role="img" aria-label="Photo of a practitioner's hands massaging a woman's upper back"
          d="M0,0 H973 V655 C860,595 720,485 560,435 C420,395 200,435 0,445 Z" fill="url(#massageTones)"/>

    <path class="band band--bottom" d="M-10,452 C200,442 420,402 560,442 C720,492 860,602 983,662"
          fill="none" stroke="url(#silverOut)" stroke-width="30"/>

    <g class="brand-mark" transform="translate(40,508)">
      <circle cx="10" cy="12" r="9" fill="none" stroke="var(--ink)" stroke-width="2"/>
      <text class="brand-name" x="26" y="8">BROOKMERE</text>
      <text class="brand-name" x="26" y="28">OSTEOPATHY</text>
    </g>

    <g class="contact">
      <g class="icon icon--phone" transform="translate(48,578)">
        <circle r="7" fill="var(--ink)"/>
        <path d="M-3,-3 q0,6 6,6 l1,-2 -2,-1 -1,1 q-2,-1 -3,-3 l1,-1 -1,-2 z" fill="#fff"/>
      </g>
      <text class="contact-line" x="63" y="582">[INSERT PHONE NUMBER]</text>

      <g class="icon icon--mail" transform="translate(48,598)">
        <circle r="7" fill="var(--ink)"/>
        <rect x="-4" y="-3" width="8" height="6" fill="none" stroke="#fff" stroke-width="1"/>
        <path d="M-4,-3 L0,1 L4,-3" fill="none" stroke="#fff" stroke-width="1"/>
      </g>
      <text class="contact-line" x="63" y="602">INFO@BROOKMEREOSTEOPATHY.EXAMPLE</text>

      <g class="icon icon--pin" transform="translate(48,618)">
        <path d="M0,8 C-3,4 -6,1 -6,-2 A6,6 0 0 1 6,-2 C6,1 3,4 0,8 Z" fill="var(--ink)"/>
        <circle cy="-2" r="2" fill="#fff"/>
      </g>
      <text class="contact-line" x="63" y="622">24 MILL LANE, BROOKMERE</text>

      <text class="web-address" x="40" y="650">WWW.BROOKMEREOSTEOPATHY.EXAMPLE</text>
    </g>
  </svg>

</main>
</body>
</html>
```